Business Card Design - Amberfield Court

We are looking at a new design for our business cards that has a modern and professional look. We run a residential aged care facility focussing on the care of residents. The cards will be used for potential clients, consultants and business opportunities in this sector. Blue and white is our main colours and would to see these colours incorporated in the design.
Industry/Entity Type
Business
Contact Information for Business Card
Amberfield Court, Darren Walsh, dwalsh@amberfieldcourt.com.au, Finance Manager, 0472 639 208, BCom, 37 Marrabel Crescent, Brindle Vale, Qld 4093.
Look and feel
Each slider illustrates characteristics of the customer's brand and the style your logo design should communicate.

```html
<!DOCTYPE html>
<html lang="en">
<head>
<meta charset="utf-8">
<title>Amberfield Court – Business Card</title>
<link href="https://fonts.googleapis.com/css2?family=Open+Sans:ital,wght@0,400;0,600;0,700;1,400&display=swap" rel="stylesheet">
<style>
  :root {
    --backdrop: #e9e4dd;
    --card-top: #f7f7f6;
    --card-bottom: #e6e8e9;
    --brand-blue: #2b4a5e;
    --ink: #2a2a2a;
    --muted: #6d6d6d;
    --rule: #4a4a4a;
    --band: rgba(92, 76, 64, 0.82);
    --band-text: #d9d4cf;
  }
  * { box-sizing: border-box; margin: 0; padding: 0; }
  html, body {
    width: 1200px;
    height: 969px;
    overflow: hidden;
    background: var(--backdrop);
    font-family: "Open Sans", Arial, sans-serif;
  }
  .card {
    position: absolute;
    left: 188px;
    top: 248px;
    width: 870px;
    height: 495px;
    border-radius: 24px;
    background: linear-gradient(160deg, var(--card-top), var(--card-bottom));
    box-shadow: 0 10px 30px rgba(0,0,0,0.12);
    overflow: hidden;
  }
  .brand {
    position: absolute;
    right: 45px;
    top: 205px;
    display: flex;
    align-items: center;
    gap: 14px;
  }
  .brand-dot {
    width: 26px;
    height: 26px;
    border-radius: 50%;
    background: var(--brand-blue);
  }
  .brand-name {
    font-size: 36px;
    font-weight: 600;
    color: var(--brand-blue);
    letter-spacing: 1px;
    text-transform: uppercase;
  }
  .edge-marker {
    position: absolute;
    left: -27px;
    top: 263px;
    width: 54px;
    height: 54px;
    border-radius: 50%;
    background: var(--brand-blue);
  }
  .person-name {
    position: absolute;
    left: 40px;
    top: 250px;
    font-size: 30px;
    font-weight: 700;
    color: var(--brand-blue);
  }
  .person-name .credential { font-size: 22px; }
  .job-title {
    position: absolute;
    left: 40px;
    top: 296px;
    font-size: 21px;
    color: var(--muted);
  }
  .title-rule {
    position: absolute;
    left: 243px;
    right: 45px;
    top: 318px;
    height: 1.5px;
    background: var(--rule);
  }
  .contact-list {
    position: absolute;
    left: 48px;
    top: 343px;
    list-style: none;
    font-size: 21px;
    color: var(--ink);
  }
  .contact-list li {
    display: flex;
    align-items: center;
    gap: 14px;
    height: 31px;
  }
  .contact-list svg { width: 20px; height: 20px; fill: var(--brand-blue); }
  .address {
    position: absolute;
    right: 45px;
    top: 343px;
    text-align: right;
    font-size: 21px;
    line-height: 31px;
    color: var(--ink);
  }
  .web-band {
    position: absolute;
    left: 40px;
    right: 45px;
    top: 430px;
    height: 33px;
    background: var(--band);
    color: var(--band-text);
    font-size: 20px;
    font-style: italic;
    letter-spacing: 1.5px;
    text-align: center;
    line-height: 33px;
  }
</style>
</head>
<body>
  <div class="card">
    <div class="brand">
      <span class="brand-dot"></span>
      <span class="brand-name">Amberfield Court</span>
    </div>

    <span class="edge-marker"></span>
    <h1 class="person-name">Darren Walsh <span class="credential">BCom</span></h1>
    <p class="job-title">Finance Manager</p>
    <span class="title-rule"></span>

    <ul class="contact-list">
      <li>
        <svg viewBox="0 0 24 24" aria-hidden="true"><path d="M6.6 10.8a15.1 15.1 0 0 0 6.6 6.6l2.2-2.2a1 1 0 0 1 1-.25 11.4 11.4 0 0 0 3.6.57 1 1 0 0 1 1 1V20a1 1 0 0 1-1 1A17 17 0 0 1 3 4a1 1 0 0 1 1-1h3.5a1 1 0 0 1 1 1c0 1.25.2 2.45.57 3.57a1 1 0 0 1-.25 1z"/></svg>
        <span>0472 639 208</span>
      </li>
      <li>
        <svg viewBox="0 0 24 24" aria-hidden="true"><path d="M2 5h20v14H2z" fill="none"/><path d="M2 5h20v2l-10 6L2 7z"/><path d="M2 9l10 6 10-6v10H2z"/></svg>
        <span>dwalsh@amberfieldcourt.com.au</span>
      </li>
    </ul>

    <address class="address" style="font-style:normal">
      37 Marrabel Crescent<br>
      Brindle Vale, Qld 4093.
    </address>

    <div class="web-band">www.amberfieldcourt.com.au</div>
  </div>
</body>
</html>
```